Dorla's Cleaners new delivery postcard

We need to advertise for our new pick up and delivery dry cleaning/laundry service.
Mens Business Shirts $2.00
Pants $4.50
Skirts $5.00
Dry Clean Shirt/Blouse $5.00
Dress $9.00
2 Piece Suits $9.00
Updates
We would like to use a 5x7 size postcard, printed on both sides. We would like to add a discount to the card for 25% off of their first order, with the flyer.
We are a famly run dry cleaners. My name is Rosalind Tupper and my cell # is 614-302-7781. We are trying to expand our business to include free pick and delivery.
If possible can you use the logo I sent some where on the postcard? The phone # for the store is 614-295-3064.
Reason: Still need to get partners approval.

```html
<!DOCTYPE html>
<html lang="en">
<head>
<meta charset="utf-8">
<title>Dorla's Cleaners – Delivery Postcard</title>
<link rel="stylesheet" href="https://fonts.googleapis.com/css2?family=Lilita+One&family=Fredoka:wght@500;600&family=Questrial&display=swap">
<style>
  :root {
    --sky-light: #eaf6fd;
    --sky-mid: #bfe2f6;
    --sky-deep: #5fb4e6;
    --panel-top: #3a8fd0;
    --panel-bottom: #1f6fb3;
    --brand-blue: #2a9ad6;
    --ink-navy: #1c4f9a;
    --accent-orange: #f07a1f;
    --accent-green: #6ab23e;
    --discount-blue: #1f8ccb;
    --white: #ffffff;
  }
  * { box-sizing: border-box; margin: 0; padding: 0; }
  html, body { width: 1200px; height: 856px; overflow: hidden; background: var(--white); }
  .postcard { position: relative; width: 1200px; height: 856px; overflow: hidden; }

  .backdrop {
    position: absolute; inset: 0;
    background:
      radial-gradient(circle at 75% 35%, var(--sky-light) 0%, transparent 45%),
      radial-gradient(circle at 20% 80%, var(--sky-mid) 0%, transparent 50%),
      linear-gradient(180deg, var(--sky-light) 0%, var(--sky-mid) 55%, var(--sky-deep) 85%);
  }

  .brand {
    position: absolute; left: 60px; top: 78px;
    display: flex; align-items: center; gap: 22px;
  }
  .brand-mark { width: 70px; height: 70px; border-radius: 50%; background: var(--brand-blue); }
  .brand-name {
    font-family: "Lilita One", sans-serif; font-size: 62px; letter-spacing: 1px;
    color: var(--brand-blue); text-transform: uppercase; line-height: 1;
  }

  .price-list {
    position: absolute; left: 0; top: 240px; width: 582px; height: 353px;
    border-radius: 0 14px 14px 0;
    background: linear-gradient(180deg, var(--panel-top), var(--panel-bottom));
    box-shadow: 0 6px 14px rgba(20, 60, 110, 0.35);
    padding: 22px 0 0 60px;
    list-style: none;
  }
  .price-item {
    display: flex; justify-content: space-between; width: 462px;
    font-family: "Questrial", sans-serif; font-size: 31px; color: var(--white);
    height: 54.8px; line-height: 54.8px;
  }

  .offer-bubble {
    position: absolute; left: 638px; top: 173px; width: 464px; height: 464px;
    border-radius: 50%;
    background: radial-gradient(circle at 50% 45%, rgba(255,255,255,0.95) 0%, rgba(235,246,253,0.9) 62%, rgba(180,220,245,0.85) 100%);
    box-shadow: inset 0 0 30px rgba(120, 180, 225, 0.6);
    text-align: center; font-family: "Fredoka", sans-serif;
  }
  .offer-percent { position: absolute; left: 0; right: 0; top: 70px; font-size: 150px; font-weight: 600; color: var(--accent-orange); line-height: 1; }
  .offer-word { position: absolute; left: 0; right: 0; top: 225px; font-size: 92px; font-weight: 500; color: var(--discount-blue); line-height: 1; }
  .offer-terms { position: absolute; left: 0; right: 0; top: 320px; font-size: 56px; font-weight: 500; color: var(--accent-green); line-height: 1; }

  .footer-wave { position: absolute; left: 0; bottom: 0; width: 1200px; height: 180px; }

  .call-to-action {
    position: absolute; left: 54px; top: 640px;
    font-family: "Lilita One", sans-serif; font-size: 64px; color: var(--ink-navy);
    -webkit-text-stroke: 0; text-shadow: 0 0 6px var(--white);
  }
  .store-phone {
    position: absolute; left: 96px; top: 718px;
    font-family: "Fredoka", sans-serif; font-weight: 600; font-size: 92px;
    color: var(--ink-navy); letter-spacing: 2px;
  }
</style>
</head>
<body>
  <main class="postcard">
    <div class="backdrop" role="img" aria-label="Soft blue background of floating soap bubbles"></div>

    <header class="brand">
      <span class="brand-mark"></span>
      <span class="brand-name">Dorla's Cleaners</span>
    </header>

    <ul class="price-list">
      <li class="price-item"><span>Mens Business Shirts</span><span>$2.00</span></li>
      <li class="price-item"><span>Pants</span><span>$4.50</span></li>
      <li class="price-item"><span>Skirts</span><span>$5.00</span></li>
      <li class="price-item"><span>Dry Clean Shirt/Blouse</span><span>$5.00</span></li>
      <li class="price-item"><span>Dress</span><span>$9.00</span></li>
      <li class="price-item"><span>2 Piece Suits</span><span>$9.00</span></li>
    </ul>

    <section class="offer-bubble">
      <div class="offer-percent">25%</div>
      <div class="offer-word">discount</div>
      <div class="offer-terms">on first order</div>
    </section>

    <svg class="footer-wave" viewBox="0 0 1200 180" preserveAspectRatio="none" aria-hidden="true">
      <path d="M0 40 C 300 90, 700 10, 1200 20 L1200 180 L0 180 Z" fill="#ffffff"/>
    </svg>

    <div class="call-to-action">Call NOW</div>
    <div class="store-phone">614-295-3064</div>
  </main>
</body>
</html>
```